Business Card Design needed for start up company Halvora

In need of a new business card designed for a start up company based in Sydney, Halvora is a new start up innovative Company, our mission it to make property accessible for everyday Australian and to become the leading Real Estate platform in Australia. We want it to be fresh and clean.

Industry/Entity Type

Financial

Contact Information for Business Card

Section for Name
Section for Title

HALVORA - The Strength of Pooling
Mobile:
Direct:

Font styles to use
Sans Serif

Colors
33a6d7
0692cd
0255a3
ffffff

Requirements
Must have
• Logo, all business card details

```html
<!DOCTYPE html>
<html lang="en">
<head>
<meta charset="utf-8">
<title>Halvora Business Card</title>
<link href="https://fonts.googleapis.com/css2?family=Jost:wght@400;500;700&display=swap" rel="stylesheet">
<style>
  :root {
    --bg: #e9e7e3;
    --navy: #1f3f78;
    --sky: #2a9fd8;
    --sky-line: #33a6d7;
    --paper: #f4f4f3;
    --white: #ffffff;
  }
  * { margin: 0; padding: 0; box-sizing: border-box; }
  html, body { width: 1200px; height: 960px; overflow: hidden; }
  body {
    position: relative;
    background: var(--bg);
    font-family: "Jost", "Futura", sans-serif;
  }
  .card {
    position: absolute;
    width: 600px;
    height: 343px;
    border-radius: 22px;
    overflow: hidden;
    box-shadow: 0 3px 6px rgba(0,0,0,0.25);
  }
  .card--front { left: 216px; top: 131px; background: var(--navy); }
  .card--back { left: 381px; top: 504px; background: var(--navy); }

  .front-top {
    position: absolute; left: 0; top: 0; width: 100%; height: 187px;
    background: var(--paper);
    border-bottom: 4px solid var(--sky-line);
  }
  .logo {
    position: absolute;
    display: flex; align-items: center; gap: 14px;
  }
  .logo__dot { width: 96px; height: 96px; border-radius: 50%; background: var(--sky); flex: none; }
  .logo__name { font-weight: 700; font-size: 62px; letter-spacing: 1px; line-height: 1; }
  .card--front .logo { left: 134px; top: 56px; }
  .card--front .logo__name { color: var(--navy); }
  .card--back .logo { left: 124px; top: 119px; }
  .card--back .logo__dot { width: 106px; height: 106px; }
  .card--back .logo__name { color: var(--white); font-size: 66px; }

  .identity {
    position: absolute; right: 309px; top: 222px;
    text-align: right; color: var(--white);
  }
  .identity__name { color: var(--sky); font-weight: 500; font-size: 21px; line-height: 24px; letter-spacing: 0.5px; }
  .identity__title { font-size: 16px; line-height: 22px; }
  .identity__address { font-size: 15px; line-height: 20px; }

  .divider {
    position: absolute; left: 312px; top: 224px; width: 1px; height: 112px;
    background: rgba(255,255,255,0.7);
  }
  .contacts {
    position: absolute; left: 336px; top: 226px;
    list-style: none; color: var(--white); font-size: 15px;
  }
  .contacts li { display: flex; align-items: center; gap: 8px; height: 19.5px; }
  .contacts svg { width: 14px; height: 14px; fill: var(--sky); flex: none; }
</style>
</head>
<body>
  <section class="card card--front">
    <div class="front-top">
      <div class="logo">
        <span class="logo__dot"></span>
        <span class="logo__name">HALVORA</span>
      </div>
    </div>
    <div class="identity">
      <p class="identity__name">MAREN HOLT</p>
      <p class="identity__title">CEO/FOUNDER</p>
      <p class="identity__address">42 Wattle Grove</p>
      <p class="identity__address">Sydney, NSW 2000</p>
    </div>
    <div class="divider"></div>
    <ul class="contacts">
      <li><svg viewBox="0 0 16 16"><path d="M3.5 1l2.5 3-1.5 1.6c.8 2 2.4 3.6 4.4 4.4L10.5 8.5l3 2.5-1.2 2.6C7 13.4 2.6 9 2.4 3.7z"/></svg>612 480 3159</li>
      <li><svg viewBox="0 0 16 16"><path d="M4.5 1h7v14h-7zM6 2.5v9.5h4V2.5z"/></svg>614 273 8806</li>
      <li><svg viewBox="0 0 16 16"><path d="M1 3.5h14v9H1zM2.2 4.5L8 9l5.8-4.5z"/></svg>maren@halvora.com</li>
      <li><svg viewBox="0 0 16 16"><circle cx="8" cy="8" r="7"/></svg>www.halvora.com</li>
    </ul>
  </section>

  <section class="card card--back">
    <div class="logo">
      <span class="logo__dot"></span>
      <span class="logo__name">HALVORA</span>
    </div>
  </section>
</body>
</html>
```